Business Card Design

We like to use greens as you will see in our logo (but not TOO much green). We are a Dental Clinic in a somewhat eccentric community. We do not like the dated sharp designs which we see many dentists use. We're looking for something bright and fresh while still maintaining the integrity of the profession. Elegance is not necessarily what we are going for... we need for the design to be "mature" but also up-lifting.

See our logo.
Updates

Project Deadline Extended
Reason: We have 5 designs which we like. But we'd like to see a few more before committing to a design.

Project Deadline Extended
Reason: We are awaiting revisions to this project. We are still welcoming designs while we wait to see if designers are able to provide to us the revisions we require in order to proceed with a selection.

Target Market(s)

Younger families - ages late 20's to early 40's

Industry/Entity Type

Business

Contact Information for Business Card

Corwel T. Banfry DDS 2730 W. Halvert Rd. Ste. 7 Alder Falls, NV 48391 (702)555-0174 FX (702)555-0189 info@BrightwellDentalCareMi.com BrigthwellDentalCareMi.com on the back of the card we need an appointment reminder (For____ Date___ Time____) with "If you are unable to keep your appointment, kindly give 48 hours notice" at the bottom. No use of teeth in the design. DOUBLE SIDED DESIGN

Requirements
Should not have
• The use of pictures of teeth

```html
<!DOCTYPE html>
<html lang="en">
<head>
<meta charset="utf-8">
<title>Brightwell Dental Care – Business Card</title>
<link rel="stylesheet" href="https://fonts.googleapis.com/css2?family=Open+Sans:ital,wght@0,400;0,700;1,400&family=Cinzel:wght@400;500&display=swap">
<style>
  :root {
    --green-deep: #1b6435;
    --green-bright: #3aa335;
    --green-leaf: #7ccc3e;
    --ink: #2b2b2b;
    --muted: #6b6b6b;
    --paper: #ffffff;
    --backdrop: #eceeea;
    --rule: #9a9a9a;
  }
  * { box-sizing: border-box; margin: 0; padding: 0; }
  html, body { width: 1200px; height: 1178px; overflow: hidden; }
  body {
    position: relative;
    background: var(--backdrop);
    font-family: "Open Sans", Arial, sans-serif;
    color: var(--ink);
  }
  .card {
    position: absolute;
    background: var(--paper);
    border-radius: 40px;
    overflow: hidden;
    border: 2px solid #d5d8d3;
    box-shadow: 0 6px 18px rgba(0,0,0,.12);
  }
  .card--front { left: 253px; top: 45px; width: 918px; height: 525px; }
  .card--back  { left: 29px;  top: 611px; width: 915px; height: 522px; }

  .swoosh { position: absolute; inset: 0; width: 100%; height: 100%; }

  .doctor {
    position: absolute; right: 32px; top: 44px;
    text-align: right; color: var(--paper);
  }
  .doctor__name { font-size: 35px; font-weight: 700; line-height: 1.2; }
  .doctor__title { font-size: 26px; font-weight: 400; line-height: 1.3; }

  .wordmark {
    position: absolute; display: flex; align-items: center; gap: 14px;
    color: var(--green-deep); font-family: "Open Sans", Arial, sans-serif; font-weight: 400;
  }
  .wordmark__dot { border-radius: 50%; background: var(--green-leaf); flex: none; }
  .wordmark__name { line-height: 1.05; }
  .card--front .wordmark { left: 51px; top: 140px; font-size: 56px; }
  .card--front .wordmark__dot { width: 46px; height: 46px; }
  .card--back .wordmark { right: 40px; top: 50px; font-size: 30px; text-align: right; }
  .card--back .wordmark__dot { width: 26px; height: 26px; }

  .contacts { position: absolute; left: 50px; top: 342px; list-style: none; }
  .contacts li { display: flex; align-items: center; gap: 8px; height: 40px; font-size: 20px; white-space: nowrap; }
  .contacts svg { width: 16px; height: 16px; fill: var(--green-deep); flex: none; }

  .address {
    position: absolute; left: 440px; top: 423px; height: 72px;
    border-left: 2px solid var(--rule); padding-left: 14px;
    font-size: 21px; line-height: 37px; font-style: normal; white-space: nowrap;
  }

  .appointment__title {
    position: absolute; left: 70px; top: 100px;
    font-family: "Cinzel", Georgia, serif; font-weight: 500;
    font-size: 35px; color: var(--green-deep); letter-spacing: 1px;
  }
  .field { position: absolute; font-size: 24px; line-height: 1; }
  .field-line {
    position: absolute; border-bottom: 2px dotted var(--muted); height: 0;
  }
  .slot {
    position: absolute; top: 308px; height: 36px; width: 165px;
    border: 2px solid var(--muted); border-radius: 5px;
  }

  .days {
    position: absolute; left: 0; top: 362px; width: 100%; height: 78px;
    background: linear-gradient(to right, var(--green-deep) 0 727px, var(--paper) 727px 731px, var(--green-bright) 731px);
    color: var(--paper); font-size: 25px; font-weight: 400;
  }
  .day { position: absolute; top: 24px; line-height: 30px; }
  .day-box {
    position: absolute; top: 23px; height: 33px; width: 56px;
    background: var(--paper); border: 2px solid #777; border-radius: 4px;
  }

  .notice {
    position: absolute; left: 0; right: 0; top: 460px;
    text-align: center; font-style: italic; font-size: 24px;
  }
</style>
</head>
<body>

<section class="card card--front" aria-label="Business card front">
  <svg class="swoosh" viewBox="0 0 918 525" preserveAspectRatio="none" aria-hidden="true">
    <path d="M0 0 H918 V352 C760 230 520 90 0 66 Z" fill="var(--green-bright)"/>
    <path d="M0 0 H918 V334 C760 215 520 80 0 60 Z" fill="var(--paper)"/>
    <path d="M0 0 H918 V322 C760 200 520 60 0 54 Z" fill="var(--green-bright)"/>
    <path d="M0 0 H918 V290 C760 175 520 48 0 50 Z" fill="var(--green-deep)"/>
  </svg>

  <div class="doctor">
    <p class="doctor__name">Corwel T. Banfry</p>
    <p class="doctor__title">DDS</p>
  </div>

  <div class="wordmark">
    <span class="wordmark__name">Brightwell<br>Dental Care</span>
    <span class="wordmark__dot"></span>
  </div>

  <ul class="contacts">
    <li><svg viewBox="0 0 20 20"><path d="M5 2l3 4-2 2c1 2 3 4 5 5l2-2 4 3-2 3C9 17 3 11 2 4z"/></svg>(702)555-0174</li>
    <li><svg viewBox="0 0 20 20"><path d="M4 9l2-5h8l2 5h2v6h-2v2h-3v-2H7v2H4v-2H2V9zm3-3l-1 3h8l-1-3z"/></svg>(702)555-0189</li>
    <li><svg viewBox="0 0 20 20"><path d="M2 8l8-5 8 5v9H2zm2 1l6 4 6-4-6-4z"/></svg>info@BrightwellDentalCareMi.com</li>
    <li><svg viewBox="0 0 20 20"><path d="M10 1a9 9 0 100 18 9 9 0 000-18zm-1 2v4H5a7 7 0 014-4zm2 0a7 7 0 014 4h-4zM3 9h6v2H3zm8 0h6v2h-6zm-6 4h4v4a7 7 0 01-4-4zm6 0h4a7 7 0 01-4 4z"/></svg>BrigthwellDentalCareMi.com</li>
  </ul>

  <address class="address">
    2730 W. Halvert Rd.<br>Ste. 7 Alder Falls, NV 48391
  </address>
</section>

<section class="card card--back" aria-label="Appointment card back">
  <h2 class="appointment__title">YOUR APPOINTMENT</h2>

  <div class="wordmark">
    <span class="wordmark__name">Brightwell<br>Dental Care</span>
    <span class="wordmark__dot"></span>
  </div>

  <span class="field" style="left:80px; top:185px;">Name :</span>
  <span class="field-line" style="left:181px; top:205px; width:670px;"></span>

  <span class="field" style="left:80px; top:249px;">Date :</span>
  <span class="field-line" style="left:181px; top:269px; width:229px;"></span>
  <span class="field" style="left:424px; top:249px;">Time :</span>
  <span class="field-line" style="left:499px; top:269px; width:245px;"></span>
  <span class="field" style="left:749px; top:249px;">am / pm</span>

  <span class="field" style="left:80px; top:313px;">Next Appointment</span>
  <span class="slot" style="left:328px;"></span>
  <span class="slot" style="left:506px;"></span>
  <span class="slot" style="left:682px;"></span>

  <div class="days">
    <span class="day" style="left:80px;">MON</span><span class="day-box" style="left:160px;"></span>
    <span class="day" style="left:227px;">TUE</span><span class="day-box" style="left:290px;"></span>
    <span class="day" style="left:358px;">WED</span><span class="day-box" style="left:434px;"></span>
    <span class="day" style="left:504px;">THU</span><span class="day-box" style="left:571px;"></span>
    <span class="day" style="left:640px;">FRI</span><span class="day-box" style="left:693px;"></span>
    <span class="day" style="left:762px;">SAT</span><span class="day-box" style="left:822px;"></span>
  </div>

  <p class="notice">If you are unable to keep your appointment, kindly give 48 hours notice</p>
</section>

</body>
</html>
```